Ward Compass Business Card Design*

We need a business card design for our company Ward Compass. Our company is specialized in providing online consulting services regarding medical institutions, hospitals and doctors. We work with patients worldwide looking to choose between healthcare providers. We have a website you may use as a reference, where we list doctors and clinics worldwide. So we target Medical providers as well as patients worldwide.
Target Market(s)
Medical Providers and patients around the world
Industry/Entity Type
Medical
Contact Information for Business Card
Salwa Kettani
CEO
+90 612 348 2175
info@wardcompass.example
www.wardcompass.example
14 Annakhil 7 H.R.B. Rabat, Morocco
Requirements
Must have
- Company logo/name on one full side, personal info and smaller logo and company name on the other side.
Nice to have
- Smart and elegant design

```html
<!DOCTYPE html>
<html lang="en">
<head>
<meta charset="utf-8">
<title>Ward Compass – Business Card</title>
<link rel="stylesheet" href="https://fonts.googleapis.com/css2?family=Montserrat:wght@300;400;700;800&family=Roboto:wght@300;400&display=swap">
<style>
  :root {
    --navy: #17396b;
    --grey: #808285;
    --ink: #3a3a3c;
    --paper: #ffffff;
    --backdrop: #e4e5e7;
  }
  * { box-sizing: border-box; margin: 0; padding: 0; }
  html, body { width: 1200px; height: 900px; overflow: hidden; }
  body {
    background: var(--backdrop);
    display: flex;
    flex-direction: column;
    align-items: center;
    justify-content: center;
    gap: 40px;
  }
  .card {
    position: relative;
    width: 700px;
    height: 400px;
    background: var(--paper);
    box-shadow: 0 2px 10px rgba(0,0,0,0.08);
  }
  .brand {
    display: flex;
    align-items: center;
    gap: 14px;
    font-family: "Montserrat", sans-serif;
    font-weight: 800;
    color: var(--navy);
    letter-spacing: 0.02em;
    text-transform: uppercase;
    white-space: nowrap;
  }
  .brand-dot {
    flex: none;
    border-radius: 50%;
    background: var(--navy);
  }

  /* Front */
  .card-front .brand {
    position: absolute;
    top: 150px;
    left: 0; right: 0;
    justify-content: center;
    font-size: 46px;
  }
  .card-front .brand-dot { width: 54px; height: 54px; }
  .front-url {
    position: absolute;
    top: 275px;
    left: 0; right: 0;
    text-align: center;
    font-family: "Montserrat", sans-serif;
    font-weight: 400;
    font-size: 17px;
    letter-spacing: 0.5em;
    color: var(--ink);
  }

  /* Back */
  .card-back .brand {
    position: absolute;
    top: 70px;
    left: 0; right: 0;
    justify-content: center;
    font-size: 32px;
  }
  .card-back .brand-dot { width: 38px; height: 38px; }
  .person {
    position: absolute;
    left: 60px;
    top: 200px;
    font-family: "Montserrat", sans-serif;
  }
  .person-name { font-weight: 800; font-size: 30px; line-height: 1.1; }
  .person-name .first { color: var(--navy); }
  .person-name .last { color: var(--grey); }
  .person-role {
    font-weight: 300;
    font-size: 20px;
    color: var(--navy);
    margin-top: 2px;
  }
  .address {
    position: absolute;
    right: 60px;
    top: 212px;
    text-align: right;
    font-family: "Roboto", sans-serif;
    font-weight: 300;
    font-size: 15px;
    line-height: 1.4;
    color: var(--ink);
  }
  .rule {
    position: absolute;
    left: 60px;
    right: 60px;
    top: 283px;
    height: 2px;
    background: var(--navy);
  }
  .contacts {
    position: absolute;
    left: 60px;
    top: 298px;
    list-style: none;
    font-family: "Roboto", sans-serif;
    font-weight: 300;
    font-size: 16px;
    color: var(--ink);
  }
  .contacts li {
    display: flex;
    align-items: center;
    gap: 12px;
    height: 28px;
  }
  .contacts svg { width: 16px; height: 16px; fill: var(--navy); flex: none; }
</style>
</head>
<body>

  <section class="card card-front" aria-label="Card front">
    <div class="brand"><span class="brand-dot"></span>Ward Compass</div>
    <p class="front-url">www.wardcompass.example</p>
  </section>

  <section class="card card-back" aria-label="Card back">
    <div class="brand"><span class="brand-dot"></span>Ward Compass</div>

    <div class="person">
      <p class="person-name"><span class="first">Salwa</span> <span class="last">Kettani</span></p>
      <p class="person-role">CEO</p>
    </div>

    <p class="address">14 Annakhil<br>7 H.R.B. Rabat, Morocco</p>

    <div class="rule"></div>

    <ul class="contacts">
      <li>
        <svg viewBox="0 0 16 16" aria-hidden="true"><path d="M3.6 1.2l2.3 2.5-1.2 1.6c.8 1.9 2.2 3.3 4.1 4.1l1.6-1.2 2.5 2.3-1.3 2.3C6.4 12.6 3.4 9.6 1.2 4.4z"/></svg>
        +90 612 348 2175
      </li>
      <li>
        <svg viewBox="0 0 16 16" aria-hidden="true"><path d="M1 3h14v10H1z M2.2 4.2L8 8.8l5.8-4.6" fill="none" stroke="#17396b" stroke-width="1.4"/><path d="M1 3h14L8 8.5z"/></svg>
        info@wardcompass.example
      </li>
      <li>
        <svg viewBox="0 0 16 16" aria-hidden="true"><circle cx="8" cy="8" r="6.5" fill="none" stroke="#17396b" stroke-width="1.4"/><path d="M1.5 8h13M8 1.5c-2.4 2.6-2.4 10.4 0 13M8 1.5c2.4 2.6 2.4 10.4 0 13" fill="none" stroke="#17396b" stroke-width="1.1"/></svg>
        www.wardcompass.example
      </li>
    </ul>
  </section>

</body>
</html>
```